Business Card Design

This is a new business to be run from my home. I have attended certificate workshops run by Dr Victor Osei who is a Master Trainer in Gentle Moves for Mobility.
I wish to communicate to people that Tai Chi is for everyone, no matter their age, gender or fitness levels. Tai Chi is taught both standing & seated.
The card should have a slightly Asian feel, mainly printed in black & white with perhaps a little soft pink &/or green.

Target Market(s)

people of all ages from 10 years up, poor fitness & mild disabilities.

Industry/Entity Type

Fitness

Contact Information for Business Card

Brookhurst Tai Chi for Fitness, Health & Relaxation

Marnie Holbrook, Certificated Leader

ph 5182 9046

Requirements
Nice to have
• a feeling of health & peace.
Should not have
• bright colours, fancy fonts

```html
<!DOCTYPE html>
<html lang="en">
<head>
<meta charset="utf-8">
<title>Brookhurst Tai Chi – Business Card</title>
<link rel="stylesheet" href="https://fonts.googleapis.com/css2?family=Pinyon+Script&family=Lato:wght@300;700;900&display=swap">
<style>
  :root {
    --card-bg: #ffffff;
    --ink: #000000;
    --figure-tone: #1a1a1a;
    --reflection: #d6d6d6;
    --reflection-fade: #f6f6f6;
    --text: #111111;
  }
  html, body {
    margin: 0;
    padding: 0;
    overflow: hidden;
    background: var(--card-bg);
  }
  .card {
    position: relative;
    width: 1200px;
    height: 741px;
    background: var(--card-bg);
    overflow: hidden;
  }
  .figure-silhouette {
    position: absolute;
    left: 66px;
    top: 44px;
    width: 290px;
    height: 330px;
    background: var(--figure-tone);
    border-radius: 18px;
  }
  .figure-reflection {
    position: absolute;
    left: 66px;
    top: 380px;
    width: 290px;
    height: 318px;
    background: linear-gradient(to bottom, var(--reflection), var(--reflection-fade));
    border-radius: 18px;
  }
  .script-title {
    position: absolute;
    left: 384px;
    top: 182px;
    margin: 0;
    font-family: "Pinyon Script", cursive;
    font-weight: 400;
    font-size: 222px;
    line-height: 1;
    color: var(--ink);
    white-space: nowrap;
    letter-spacing: 2px;
  }
  .script-title .gap { display: inline-block; width: 34px; }
  .details {
    position: absolute;
    left: 390px;
    top: 480px;
    width: 600px;
    text-align: center;
    color: var(--text);
    font-family: "Lato", sans-serif;
  }
  .business-name {
    margin: 0 0 6px;
    font-weight: 900;
    font-size: 35px;
    line-height: 1.2;
  }
  .detail-line {
    margin: 0;
    font-weight: 300;
    font-size: 28px;
    line-height: 46px;
  }
</style>
</head>
<body>
  <div class="card">
    <div class="figure-silhouette" role="img" aria-label="Black silhouette of a tai chi practitioner in a low lunging pose"></div>
    <div class="figure-reflection" role="img" aria-label="Faint grey mirrored reflection of the tai chi figure"></div>
    <h1 class="script-title">Tai<span class="gap"></span>Chi</h1>
    <div class="details">
      <p class="business-name">Brookhurst Tai Chi</p>
      <p class="detail-line">For Fitness, Health &amp; Relaxation</p>
      <p class="detail-line">Marnie Holbrook (Certificated Leader)</p>
      <p class="detail-line">Tel: 5182 9046</p>
    </div>
  </div>
</body>
</html>
```